KBT Business Cards

We require business cards for our business. We would like a matte black back to the card, with our logo centred in the middle. The front side of the card is open to design.

Target Market(s)

Clients looking for legal services (professional)

Industry/Entity Type

Legal

Contact Information for Business Card

Doran Kelbrath
Partner
Mobile: 0461 738 524
Email: doran@kbtlaw.co
Website: www.kbtlaw.co
Level 3, 118 Wendmore Street
Sydney NSW 2000

Font styles to use
Other font styles liked:
• Avenir

Colors
f04a50
ffffff
1b1b1b

Requirements
Must have
• Black back with logo included in the centre of the card.
• Our font is Avenir.

```html
<!DOCTYPE html>
<html lang="en">
<head>
<meta charset="utf-8">
<title>KBT Business Cards</title>
<link rel="stylesheet" href="https://fonts.googleapis.com/css2?family=Nunito+Sans:wght@400;600;700;800&display=swap">
<style>
  :root {
    --stage: #2b2b2d;
    --card: #1b1b1b;
    --ink: #ffffff;
    --ink-soft: #e6e6e6;
    --accent: #d42a4f;
    --gloss: #0c0c0c;
    --gloss-edge: #303030;
  }
  * { box-sizing: border-box; margin: 0; padding: 0; }
  html, body {
    width: 1200px; height: 800px; overflow: hidden;
    background: var(--stage);
    font-family: "Nunito Sans", "Avenir", sans-serif;
  }
  .sheet {
    width: 1200px; height: 800px;
    display: flex; align-items: center; justify-content: center; gap: 40px;
  }
  .card {
    position: relative;
    width: 540px; height: 309px;
    background: var(--card);
    border-radius: 18px;
    box-shadow: 0 18px 40px rgba(0,0,0,.45);
    overflow: hidden;
  }

  /* Back: matte black with centred firm name */
  .card--back { display: flex; align-items: center; justify-content: center; }
  .back-mark { display: flex; align-items: center; gap: 18px; }
  .back-mark__square {
    width: 54px; height: 54px;
    background: var(--gloss);
    box-shadow: inset 0 0 0 1px var(--gloss-edge);
  }
  .back-mark__name {
    color: var(--gloss);
    font-weight: 800; font-size: 22px; line-height: 1.02;
    letter-spacing: .5px; text-transform: uppercase;
    text-shadow: 0 1px 0 var(--gloss-edge);
  }

  /* Front: firm name and contact details */
  .card--front { padding: 52px 0 0 40px; }
  .firm-name {
    color: var(--ink);
    font-weight: 800; font-size: 25px; line-height: 1.02;
    text-transform: uppercase; letter-spacing: .3px;
  }
  .person { margin-top: 20px; }
  .person__name {
    color: var(--accent);
    font-weight: 800; font-size: 13px; text-transform: uppercase; letter-spacing: .3px;
  }
  .person__role { color: var(--ink-soft); font-size: 12px; font-weight: 600; }
  .address { margin-top: 12px; color: var(--ink-soft); font-size: 12px; line-height: 1.35; font-weight: 600; }
  .contacts { list-style: none; margin-top: 2px; }
  .contacts li {
    display: flex; align-items: center; gap: 8px;
    color: var(--ink-soft); font-size: 12px; line-height: 1.35; font-weight: 600;
  }
  .contacts svg { width: 11px; height: 11px; flex: none; }
</style>
</head>
<body>
<main class="sheet">

  <section class="card card--back" aria-label="Card back">
    <div class="back-mark">
      <div class="back-mark__square"></div>
      <p class="back-mark__name">Kelbrath<br>Brandt Tarrow<br>Legal</p>
    </div>
  </section>

  <section class="card card--front" aria-label="Card front">
    <h1 class="firm-name">Kelbrath<br>Brandt Tarrow<br>Legal</h1>
    <div class="person">
      <p class="person__name">Doran Kelbrath</p>
      <p class="person__role">Partner</p>
    </div>
    <p class="address">Level 3, 118 Wendmore Street<br>Sydney NSW 2000</p>
    <ul class="contacts">
      <li>
        <svg viewBox="0 0 12 12" aria-hidden="true"><rect x="1.5" y="1.5" width="9" height="9" fill="none" stroke="var(--accent)" stroke-width="1.5"/></svg>
        0461 738 524
      </li>
      <li>
        <svg viewBox="0 0 12 12" aria-hidden="true"><rect x="0.5" y="2" width="11" height="8" fill="var(--accent)"/><path d="M0.8 2.4 6 6.6 11.2 2.4" fill="none" stroke="var(--card)" stroke-width="1.1"/></svg>
        doran@kbtlaw.co
      </li>
      <li>
        <svg viewBox="0 0 12 12" aria-hidden="true"><circle cx="6" cy="6" r="5.5" fill="var(--accent)"/><path d="M0.5 6h11M6 .5c-2.4 3-2.4 8 0 11M6 .5c2.4 3 2.4 8 0 11" fill="none" stroke="var(--card)" stroke-width=".8"/></svg>
        www.kbtlaw.co
      </li>
    </ul>
  </section>

</main>
</body>
</html>
```